New Wordpress Design Project - Australian native plant nursery

I'm Seeking a wordpress website with landing page with contact details and social links, that page will link to another 4 pages. I'm happy to just add in the information once the template is set up (draft text provided on word doc).
Needing pages of information pages for:
- Nursery, what we carry and that we provide garden design services, pictures of plants and gardens
- Native flowers & what we provide, flower arrangements for weddings, special occasions, pictures
- Giftwear short blurb that we carry local artisan giftwear, pictures
- about us with history of the nursery & pictures
* Also wanting a link for e-gift cards. The link will go to an external page (square) so I don’t need to set up the website for purchases.
Social media links
Social links
https://www.facebook.com/ThePebbleHollowGarden
https://www.instagram.com/thepebblehollowgardennursery

Two local native nursery websites that I like the style of:
https://www.brimbarkstemnursery.com.au/
https://www.telvoni.com.au/

I'm using two versions of our logo, we have the smaller circle and then the other logo which is stretched out. We have used the second design for our signs at the nursery, I've asked the sign guy for a copy of the design as I don't currently have one. I have vector files of the other design.

We have wordpress set up with elemantor and hosting with godaddy, I can send you the logon details once design is confirmed.

Target Market(s)

Anyone who likes gardening, we have a pretty even spread of customers across male/female and all ages

Industry/Entity Type

Garden centre with native plants, flowers and giftwear

Coding

Coded - Design and coding required

Colors
0054AA
0677BA
7BADD7
CADEEF
E8F1F8
0094D4
00A9DD
6FCCEA
C7EBF8
E9F6FB
00AB8E
00BBA5
67D7C9
C6EFE9
E9F9F6

Requirements
Must have
• Organic/modern/minimalist design
Nice to have
• Blue/white/green, flannel flowers as per logo

```html
<!DOCTYPE html>
<html lang="en">
<head>
<meta charset="utf-8">
<title>The Pebble Hollow Garden – Australian Native Plant Nursery</title>
<link rel="stylesheet" href="https://fonts.googleapis.com/css2?family=Merriweather:ital,wght@0,400;0,700;1,700&family=Lato:wght@400;700&display=swap">
<style>
:root{
  --green:#00a182;
  --green-dark:#008a70;
  --teal:#00a39a;
  --blue:#0a63a8;
  --navy:#12285e;
  --ink:#1d1d1d;
  --text:#3a3a3a;
  --white:#ffffff;
  --footer:#23272a;
  --rule:#8a8f80;
}
*{box-sizing:border-box;margin:0;padding:0}
html,body{width:1200px;height:3777px;overflow:hidden}
body{position:relative;background:var(--white);font-family:"Lato",sans-serif;color:var(--text)}
a{color:inherit;text-decoration:none}

/* header */
.topbar{position:absolute;left:0;top:0;width:1200px;height:66px;background:var(--white)}
.topbar__contacts{position:absolute;right:112px;top:16px;display:flex;align-items:center;gap:18px;font-family:"Merriweather",serif;font-size:14px;color:var(--ink)}
.topbar__item{display:flex;align-items:center;gap:10px;white-space:nowrap}
.icon-dot{width:32px;height:32px;border-radius:50%;border:1.5px solid #9fb6d6;display:flex;align-items:center;justify-content:center;box-shadow:0 2px 3px rgba(0,0,0,.15)}
.social-top{display:flex;gap:10px;margin-left:14px}
.social-top a{width:32px;height:32px;border-radius:50%;border:1.5px solid #9fb6d6;box-shadow:0 2px 3px rgba(0,0,0,.15);display:block}
.navbar{position:absolute;left:0;top:66px;width:1200px;height:69px;background:var(--green)}
.nav{position:absolute;left:339px;top:0;height:69px;display:flex;align-items:center;gap:36px;font-family:"Merriweather",serif;font-size:16px;color:var(--white);white-space:nowrap}
.nav a.is-active{text-decoration:underline;text-underline-offset:5px}
.nav__cta{position:absolute;left:866px;top:15px;width:136px;height:42px;border-radius:21px;background:var(--white);color:var(--navy);font-family:"Merriweather",serif;font-size:16px;display:flex;align-items:center;justify-content:center}
.nav__search{position:absolute;left:1031px;top:21px;width:28px;height:28px;border-radius:50%;background:var(--white);display:flex;align-items:center;justify-content:center}
.brand-badge{position:absolute;left:115px;top:-3px;width:146px;height:146px;border-radius:50%;background:var(--white);display:flex;align-items:center;justify-content:center;z-index:3}
.brand-badge__ring{width:126px;height:126px;border-radius:50%;border:1.5px solid #555;display:flex;align-items:center;justify-content:center;text-align:center;font-family:"Merriweather",serif;font-size:13px;line-height:1.25;color:#444}

/* hero */
.hero{position:absolute;left:0;top:135px;width:1200px;height:565px;background:radial-gradient(ellipse at 70% 45%,#e9ead2 0%,#c9cda5 28%,#6f7a4c 60%,#3d4a2c 100%)}
.hero__disc{position:absolute;left:378px;top:69px;width:404px;height:404px;border-radius:50%;background:var(--green);border:5px solid var(--white);text-align:center;color:var(--white)}
.hero__eyebrow{margin-top:146px;font-family:"Merriweather",serif;font-size:19px;letter-spacing:3px}
.hero__title{font-family:"Merriweather",serif;font-weight:400;font-size:45px;line-height:54px;margin-top:6px}
.hero__btn{display:inline-block;margin-top:14px;padding:11px 22px;border-radius:26px;background:var(--white);color:var(--navy);font-family:"Merriweather",serif;font-weight:700;font-size:18px}

.deals{position:absolute;left:0;top:700px;width:1200px;height:85px;background:var(--green);display:flex;align-items:center;justify-content:center;font-family:"Merriweather",serif;font-style:italic;font-weight:700;font-size:26px;letter-spacing:2px;color:var(--white)}

/* feature rows */
.feature__media{position:absolute;height:500px}
.feature__media--left{left:0;width:598px;border-radius:0 300px 300px 0/0 250px 250px 0}
.feature__media--right{left:598px;width:602px;border-radius:300px 0 0 300px/250px 0 0 250px}
.arrow{position:absolute;width:32px;height:24px}
.feature__copy{position:absolute;width:450px;text-align:center}
.feature__title{font-family:"Merriweather",serif;font-weight:700;font-size:43px;color:var(--green);margin-bottom:8px}
.feature__copy p{font-size:15px;line-height:27.5px;margin-bottom:27px}
.btn-green{display:inline-block;padding:13px 22px;border-radius:28px;background:var(--green);color:var(--white);font-family:"Merriweather",serif;font-weight:700;font-size:19px;box-shadow:0 4px 5px rgba(0,0,0,.25);margin-top:-2px}

/* about */
.about{position:absolute;left:0;top:2497px;width:1200px;height:504px;background:linear-gradient(180deg,#009c8c 0%,#0b7fa3 55%,#0c63a6 100%)}
.about__title{position:absolute;left:110px;top:73px;font-family:"Merriweather",serif;font-weight:700;font-size:40px;line-height:51px;color:var(--white)}
.about__text{position:absolute;left:112px;top:196px;width:500px;font-size:15px;line-height:25.5px;color:var(--white)}
.about__text p{margin-bottom:25px}
.about__btn{position:absolute;left:113px;top:368px;padding:14px 28px;border-radius:28px;background:var(--white);color:var(--green);font-family:"Merriweather",serif;font-weight:700;font-size:19px}
.about__photo{position:absolute;left:685px;top:56px;width:394px;height:394px;border-radius:50%;border:4px solid var(--white);background:linear-gradient(160deg,#b9c7a8 0%,#7aa690 40%,#3d6d78 100%)}

/* nursery now */
.nursery{position:absolute;left:0;top:3001px;width:1200px;height:314px;text-align:center}
.nursery__title{margin-top:51px;font-family:"Merriweather",serif;font-weight:700;font-size:40px;color:var(--green)}
.nursery__sub{margin-top:12px;font-family:"Merriweather",serif;font-weight:700;font-size:21px;color:var(--ink)}
.nursery__text{margin:22px auto 0;width:820px;font-size:15px;line-height:30px;color:var(--ink)}

/* footer */
.footer{position:absolute;left:0;top:3315px;width:1200px;height:462px;background:var(--footer);color:var(--white)}
.footer__heading{position:absolute;font-family:"Merriweather",serif;font-weight:700;font-size:22px}
.form{position:absolute;left:113px;top:114px;width:339px}
.form__row{display:flex;gap:6px;margin-bottom:8px}
.field{height:39px;background:var(--white);border-radius:2px;color:#444;font-size:10px;padding:12px 20px}
.field--half{width:166px}
.field--full{width:339px}
.field--area{height:71px}
.form__submit{display:inline-block;margin-top:2px;padding:10px 30px;border-radius:18px;background:var(--white);color:var(--navy);font-weight:700;font-size:12px}
.contact-list{position:absolute;left:527px;top:113px;list-style:none;font-size:14px;line-height:20px}
.contact-list li{display:flex;align-items:flex-start;gap:12px;margin-bottom:22px}
.contact-list .icon-dot{width:26px;height:26px;border:1.5px solid #9fb6d6;box-shadow:none;flex:none}
.contact-list li span{padding-top:3px}
.footer__brand{position:absolute;left:886px;top:75px;width:168px;height:168px;border-radius:50%;border:2px solid var(--white);display:flex;align-items:center;justify-content:center;text-align:center;font-family:"Merriweather",serif;font-size:17px;line-height:1.3}
.social-foot{position:absolute;left:883px;top:260px;display:flex;gap:26px}
.social-foot a{width:32px;height:32px;border-radius:50%;background:var(--green);display:block}
.footer__rule{position:absolute;left:110px;top:374px;width:978px;height:1px;background:var(--rule)}
.footer__copy{position:absolute;left:0;top:404px;width:1200px;text-align:center;font-size:14px}
</style>
</head>
<body>

<header class="topbar">
  <div class="topbar__contacts">
    <span class="topbar__item">
      <span class="icon-dot"><svg width="14" height="10" viewBox="0 0 14 10"><rect x="0.5" y="0.5" width="13" height="9" rx="1" fill="var(--navy)"/><path d="M1 1l6 4.5L13 1" stroke="#fff" fill="none" stroke-width="1.2"/></svg></span>
      info@thepebblehollowgarden.com.au
    </span>
    <span class="topbar__item">
      <span class="icon-dot"><svg width="14" height="14" viewBox="0 0 24 24"><path d="M6.6 10.8a15 15 0 006.6 6.6l2.2-2.2a1 1 0 011-.25 11.4 11.4 0 003.6.57 1 1 0 011 1V20a1 1 0 01-1 1A17 17 0 013 4a1 1 0 011-1h3.5a1 1 0 011 1c0 1.25.2 2.45.57 3.57a1 1 0 01-.25 1z" fill="var(--navy)"/></svg></span>
      +61 2 4000 7182
    </span>
    <nav class="social-top" aria-label="Social profiles">
      <a href="#" aria-label="Social profile 1"></a>
      <a href="#" aria-label="Social profile 2"></a>
      <a href="#" aria-label="Social profile 3"></a>
      <a href="#" aria-label="Social profile 4"></a>
    </nav>
  </div>
</header>

<div class="brand-badge"><div class="brand-badge__ring">The Pebble<br>Hollow<br>Garden</div></div>

<div class="navbar">
  <nav class="nav" aria-label="Main">
    <a href="#" class="is-active">Home</a>
    <a href="#">Our Story</a>
    <a href="#">Services</a>
    <a href="#">Gallery</a>
    <a href="#">Testimonials</a>
  </nav>
  <a class="nav__cta" href="#">Contact Us</a>
  <span class="nav__search"><svg width="12" height="12" viewBox="0 0 12 12"><circle cx="5" cy="5" r="3.5" stroke="var(--green)" stroke-width="1.6" fill="none"/><path d="M7.6 7.6L10.5 10.5" stroke="var(--green)" stroke-width="1.6"/></svg></span>
</div>

<section class="hero" role="img" aria-label="Close-up of clusters of small cream native everlasting flowers among green foliage">
  <div class="hero__disc">
    <div class="hero__eyebrow">WELCOME TO</div>
    <h1 class="hero__title">The Pebble<br>Hollow Garden</h1>
    <a class="hero__btn" href="#">Buy E-gift cards</a>
  </div>
</section>

<div class="deals">WEEKEND MEGA DEALS</div>

<!-- Native plants -->
<div class="feature__media feature__media--left" style="top:785px;background:linear-gradient(135deg,#6a4a3a 0%,#b4566d 40%,#e2628a 65%,#8f6a5c 100%)" role="img" aria-label="Pink and white paper daisies with pink native flowering shrubs">
  <svg class="arrow" style="left:32px;top:458px" viewBox="0 0 32 24"><path d="M30 12H4M13 3L3 12l10 9" stroke="#fff" stroke-width="4" fill="none"/></svg>
  <svg class="arrow" style="left:337px;top:457px" viewBox="0 0 32 24"><path d="M2 12h26M19 3l10 9-10 9" stroke="#fff" stroke-width="4" fill="none"/></svg>
</div>
<div class="feature__copy" style="left:646px;top:838px">
  <h2 class="feature__title">Native plants</h2>
  <p>At our nursery, we provide native plants that thrive in their local environment. Native plants are essential for preserving biodiversity, and they support pollinators and other wildlife while reducing human impact on the environment.</p>
  <p>At our nursery, we offer a wide selection of native plants that are suitable for a variety of different environments, and we provide planting and care instructions to ensure that your plants thrive once they're in the ground.</p>
  <a class="btn-green" href="#">Learn More</a>
</div>

<!-- Flowers -->
<div class="feature__copy" style="left:107px;top:1378px">
  <h2 class="feature__title">Flowers</h2>
  <p>At the nursery, we specialize in creating unique arrangements using locally sourced native Australian flowers. Our team of experienced florists are passionate about showcasing the beauty of our country's flora and fauna through unique and beautiful bespoke floral designs.</p>
  <p>Our native flower arrangements are perfect for any occasion – from weddings and corporate events to simple gifts for loved ones. The vibrant colours and textures of our native flowers can add a touch of the Australian landscape to any space.</p>
  <a class="btn-green" href="#">Learn More</a>
</div>
<div class="feature__media feature__media--right" style="top:1335px;background:radial-gradient(ellipse at 45% 40%,#e07aa0 0%,#c85a82 30%,#6d7f55 70%,#3e5a35 100%)" role="img" aria-label="Pink kangaroo paw flowers in close-up">
  <svg class="arrow" style="left:228px;top:458px" viewBox="0 0 32 24"><path d="M30 12H4M13 3L3 12l10 9" stroke="#fff" stroke-width="4" fill="none"/></svg>
  <svg class="arrow" style="left:534px;top:460px" viewBox="0 0 32 24"><path d="M2 12h26M19 3l10 9-10 9" stroke="#fff" stroke-width="4" fill="none"/></svg>
</div>

<!-- Giftwear -->
<div class="feature__media feature__media--left" style="top:1923px;width:607px;background:linear-gradient(135deg,#5a6a4a 0%,#d9b7c0 35%,#e8d98a 60%,#7a5a60 100%)" role="img" aria-label="Mixed bouquet of native proteas, flannel flowers and waxflowers">
  <svg class="arrow" style="left:40px;top:460px" viewBox="0 0 32 24"><path d="M30 12H4M13 3L3 12l10 9" stroke="#fff" stroke-width="4" fill="none"/></svg>
  <svg class="arrow" style="left:346px;top:459px" viewBox="0 0 32 24"><path d="M2 12h26M19 3l10 9-10 9" stroke="#fff" stroke-width="4" fill="none"/></svg>
</div>
<div class="feature__copy" style="left:648px;top:1975px">
  <h2 class="feature__title">Giftwear</h2>
  <p>We are proud to offer a wide range of unique and high-quality gifts that celebrate the natural beauty of Australia's native flora and fauna. From beautifully scented candles to stunning artworks, our gift selection is sure to please.</p>
  <p>Our giftware collection features a range of products that have been designed and crafted by local artisans and small businesses. We believe in supporting our community and showcasing the amazing talent and creativity that can be found here in Australia.</p>
  <a class="btn-green" href="#">Learn More</a>
</div>

<!-- About -->
<section class="about">
  <h2 class="about__title">About Australian Native<br>Plant Nursery</h2>
  <div class="about__text">
    <p>The Pebble Hollow Garden business, that has been providing plants, flowers and native giftware to the Central Coast and surrounding areas since 2001.</p>
    <p>Over this time, we have established a strong connection with the community and provided expert native advice.</p>
  </div>
  <a class="about__btn" href="#">Read More</a>
  <div class="about__photo" role="img" aria-label="Nursery team members standing together inside the shop"></div>
</section>

<!-- Nursery now -->
<section class="nursery">
  <h2 class="nursery__title">The Nursery Now</h2>
  <p class="nursery__sub">Since then concentrating strictly on native only</p>
  <p class="nursery__text">The business was originally established by Maren and Isla, ** later departed and Delia and Rosalind.<br>Maren Hollis has been in the native plant industry for most of her life. She has been involved in the propagation, wholesale, retail, floral design and promotion of native plants.</p>
</section>

<!-- Footer -->
<footer class="footer">
  <h3 class="footer__heading" style="left:112px;top:65px">Get In Touch</h3>
  <form class="form">
    <div class="form__row"><div class="field field--half">Name</div><div class="field field--half">Phone Number</div></div>
    <div class="form__row"><div class="field field--full">Email Address</div></div>
    <div class="form__row"><div class="field field--full field--area">Message</div></div>
    <span class="form__submit">SUBMIT NOW</span>
  </form>

  <h3 class="footer__heading" style="left:527px;top:65px">Contact Us</h3>
  <ul class="contact-list">
    <li><span class="icon-dot"><svg width="12" height="12" viewBox="0 0 24 24"><path d="M6.6 10.8a15 15 0 006.6 6.6l2.2-2.2a1 1 0 011-.25 11.4 11.4 0 003.6.57 1 1 0 011 1V20a1 1 0 01-1 1A17 17 0 013 4a1 1 0 011-1h3.5a1 1 0 011 1c0 1.25.2 2.45.57 3.57a1 1 0 01-.25 1z" fill="none" stroke="#fff" stroke-width="1.8"/></svg></span><span>+61 2 4000 7182</span></li>
    <li><span class="icon-dot"><svg width="13" height="10" viewBox="0 0 14 10"><rect x="0.7" y="0.7" width="12.6" height="8.6" rx="1" fill="none" stroke="#fff" stroke-width="1.2"/><path d="M1 1l6 4.5L13 1" stroke="#fff" fill="none" stroke-width="1.2"/></svg></span><span>info@thepebblehollowgarden.com.au</span></li>
    <li><span class="icon-dot"><svg width="11" height="13" viewBox="0 0 12 14"><path d="M6 13s5-4.5 5-8A5 5 0 001 5c0 3.5 5 8 5 8z" fill="none" stroke="#fff" stroke-width="1.3"/><circle cx="6" cy="5" r="1.8" fill="none" stroke="#fff" stroke-width="1.2"/></svg></span><span>27 Banksia Ridge Road, Kelmarsh,<br>NSW, Australia, 2261</span></li>
    <li><span class="icon-dot"><svg width="13" height="13" viewBox="0 0 14 14"><circle cx="7" cy="7" r="5.8" fill="none" stroke="#fff" stroke-width="1.3"/><path d="M7 3.5V7l2.5 1.5" stroke="#fff" stroke-width="1.3" fill="none"/></svg></span><span>Mon to Fri: 8.30 to 5.00</span></li>
  </ul>

  <div class="footer__brand">The Pebble<br>Hollow<br>Garden</div>
  <nav class="social-foot" aria-label="Social profiles">
    <a href="#" aria-label="Social profile 1"></a>
    <a href="#" aria-label="Social profile 2"></a>
    <a href="#" aria-label="Social profile 3"></a>
    <a href="#" aria-label="Social profile 4"></a>
  </nav>

  <div class="footer__rule"></div>
  <p class="footer__copy">Copyrights@2023.The Pebble Hollow Garden &nbsp;&nbsp; | &nbsp;&nbsp; All Rights Reserved</p>
</footer>

</body>
</html>
```